New design and logo for www.vornbau.com

Hi, we need a new design for the site www.vornbau.com
It's a scale modelling e-commerce website (no RC models or die cast models, only static models to build) which is a highly technical hobby (exact scale reproduction from passionated starting with the kit we sell using different material (paint, airbrush...)). Main fields are military aircrafts, military vehicles and scale figures. They are also less important fields like reference books, boats, civilian vehicles, tools like aibrushes, paints and so on.
Every scale model come with plans for mounting the items (mainly on plastic sprues), instructions for painting and most of them have decals to apply.
We don't want a military feeling, and visitors must understand immediately that our site is not about RC models or die cast models but are kits to build. They are not toys, customers are mainly adults aroud 30-50 (hobby starting aroud 14 years old), mainly mens but a few girls are in the hobby too (mainly in figures).
We would like to get rid of the right banner and have a search engine (actually on left top of the menu) and menu (actually on left) on all the pages. We need the main page banners for new products or announcements and the first page must show the last added product.
The product's list (click on any link on left) must be improved and the product's detail too.
Here are the page sample to make template for (same design but we need to know how to build them):
Main page: http://www.vornbau.com/
Product's list: http://www.vornbau.com/planes-1_48-aircraft-kits-c-21_27.html
Product's detail: http://www.vornbau.com/ketrova-kv81342-1_48-hollmann-hm-204b-wendel-foreign-af-p-71846.html
Those items must be visible at any time (design can be changed without problem) :
The cart with content once you add something on it
The language seletor
The currency selector
Chatterly Like link
link to account
newsletter register form (actually not visible on our site, only a field for entering the email but should be appealing)
You are free to put all other informations (contact, general informations, payments...) where you want
Design must be done in a way it will improve the sales and feel confident with the site. We have no preferences for colors and disposition, new logo proposal is also highly welcome (with eventually an extra fee, but we won't start 2 projects).
If you have any question, please feel free to contact us.
Thank you for reading, do your best and good luck!
Target Market(s)
Mainly mens 30-50
Industry/Entity Type
E-Commerce
Requirements
Must have
- Understand it's a scale modeling site and not toy, die cast or RC
The language seletor
The currency selector
Chatterly Like link
link to account
Nice to have
- New logo

```html
<!DOCTYPE html>
<html lang="en">
<head>
<meta charset="utf-8">
<title>Vornbau.com – model kits and detail sets</title>
<link href="https://fonts.googleapis.com/css2?family=Cabin:wght@400;500;600&display=swap" rel="stylesheet">
<style>
:root{
  --orange:#f7941d;
  --orange-light:#fbb03b;
  --orange-text:#f58a1f;
  --green:#5fae1c;
  --green-light:#7cc52b;
  --ink:#333;
  --muted:#7a7a7a;
  --line:#e2e2e2;
  --card-border:#dcdcdc;
  --footer:#f4f4f4;
}
*{box-sizing:border-box;margin:0;padding:0}
html,body{width:797px;height:1200px;overflow:hidden}
body{position:relative;background:#fff;font-family:"Cabin",sans-serif;color:var(--ink)}
.abs{position:absolute}
.top-strip{left:0;top:0;width:797px;height:4px;background:#e6e6e6}
.account-links{right:49px;top:12px;font-size:9px;color:#555}
.account-links span{margin:0 5px;color:#999}
.logo{left:48px;top:40px;display:flex;align-items:center;gap:5px}
.logo-mark{width:12px;height:12px;background:#777}
.logo-name{font-size:22px;font-weight:600;color:var(--orange-light)}
.selector-label{top:53px;font-size:10px;color:#555}
.selector{top:49px;height:20px;border:1px solid #ccc;font-size:8.5px;color:#888;padding:5px 6px}
.caret{position:absolute;right:6px;top:8px;width:0;height:0;border-left:3.5px solid transparent;border-right:3.5px solid transparent;border-top:4px solid #555}
.nav{left:43px;top:83px;width:710px;height:36px;background:linear-gradient(#fba02a,var(--orange));display:flex;border:1px solid #f08a12}
.nav a{color:#fff;text-decoration:none;font-size:13px;font-weight:500;line-height:34px;padding:0 16px;border-right:1px solid rgba(255,255,255,.35)}
.nav a:last-child{border:none}
.hero{left:43px;top:119px;width:710px;height:255px;border:1px solid #e3e3e3;border-top:none;box-shadow:0 1px 3px rgba(0,0,0,.08)}
.hero-photo{left:49px;top:121px;width:697px;height:248px;background:radial-gradient(ellipse at 40% 55%,#b79d63 0%,#9c8554 30%,#d9d6d0 65%,#e8e8e8 100%)}
.hero-arrows{left:62px;top:342px}
.finder{left:543px;top:132px;width:198px;height:219px;background:#fff;border:1px solid #e0e0e0}
.finder-head{height:32px;background:linear-gradient(var(--green-light),var(--green));color:#fff;font-size:14px;padding:8px 17px}
.finder label{position:absolute;left:18px;font-size:9.5px;color:#555}
.field{position:absolute;left:18px;width:161px;height:20px;border:1px solid #d5d5d5;border-radius:3px;box-shadow:inset 0 1px 2px rgba(0,0,0,.06)}
.find-btn{position:absolute;left:104px;top:179px;width:74px;height:22px;border-radius:3px;background:linear-gradient(#ff8a2a,#f06a0a);color:#fff;font-size:10px;text-align:center;line-height:22px;border:1px solid #e06008}
.intro-title{left:43px;top:394px;font-size:17px;font-weight:500;color:#333}
.intro-text{left:43px;top:420px;width:480px;font-size:9.5px;line-height:17px;color:#888}
.perks{font-size:9.2px;color:#555;list-style:none}
.perks li{height:20.5px;padding-left:10px;position:relative}
.perks li::before{content:"";position:absolute;left:0;top:3px;border-top:3.5px solid transparent;border-bottom:3.5px solid transparent;border-left:4px solid var(--orange)}
.rule{left:38px;top:577px;width:485px;height:1px;background:var(--line)}
.section-title{left:44px;top:593px;font-size:15px;color:var(--orange-text)}
.card{width:114px;height:142px;border:1px solid var(--card-border);border-radius:2px;box-shadow:0 2px 3px rgba(0,0,0,.08);text-align:center}
.card-img{position:absolute;left:15px;top:13px;width:83px;height:59px}
.card-text{position:absolute;left:6px;right:6px;top:83px;font-size:9.2px;line-height:14.5px;color:var(--muted)}
.side-box{border:1px solid #e3e3e3;background:#fff}
.new-head{height:29px;background:linear-gradient(#fba02a,var(--orange));color:#fff;font-size:13px;padding:7px 14px}
.new-photo{left:571px;top:430px;width:173px;height:69px;background:linear-gradient(135deg,#d8c6a6 0%,#a27a52 40%,#7c5a3c 70%,#c9c0b2 100%)}
.new-text{left:572px;top:506px;font-size:10px;line-height:14px;color:#333}
.cat-head{height:34px;background:linear-gradient(#fff,#eee);font-size:14px;padding:11px 18px;color:#333}
.cat{position:absolute;font-size:9.5px;color:#333;padding-left:14px}
.cat::before{content:"";position:absolute;left:0;top:3px;border-top:3px solid transparent;border-bottom:3px solid transparent;border-left:3.5px solid #aaa}
.cat.main{left:578px;width:155px;border-bottom:1px solid #eee;padding-bottom:3px}
.cat.sub{left:591px;color:#555}
.footer{left:0;top:1113px;width:797px;height:87px;background:var(--footer);box-shadow:inset 0 4px 5px -3px rgba(0,0,0,.08)}
.footer-links{left:43px;top:1138px;font-size:10px;color:#333}
.footer-links span{margin:0 4px;color:#555}
.copyright{left:44px;top:1162px;font-size:7.5px;color:#555}
.social{top:1146px;width:17px;height:17px;border-radius:3px}
</style>
</head>
<body>
<div class="abs top-strip"></div>
<div class="abs account-links">My Account<span>|</span>Cart Contents<span>|</span>Checkout</div>

<div class="abs logo"><div class="logo-mark"></div><div class="logo-name">Vornbau.com</div></div>
<div class="abs selector-label" style="left:486px">Currency</div>
<div class="abs selector" style="left:532px;width:56px">CHF<i class="caret"></i></div>
<div class="abs selector-label" style="left:612px">Select Language</div>
<div class="abs selector" style="left:686px;width:60px">English<i class="caret"></i></div>

<nav class="abs nav">
  <a href="#">Home</a><a href="#">New Products</a><a href="#">Sales</a><a href="#">Preorder</a><a href="#">About Us</a><a href="#">Contact Us</a>
</nav>

<div class="abs hero"></div>
<div class="abs hero-photo" role="img" aria-label="Close-up photo of a painted sand-coloured anti-aircraft tank model kit"></div>
<svg class="abs hero-arrows" width="26" height="16" viewBox="0 0 26 16"><path d="M8 2 L2 8 L8 14 M16 2 L22 8 L16 14" fill="none" stroke="#666" stroke-width="1.5"/></svg>

<form class="abs finder">
  <div class="finder-head">Quick Find Product</div>
  <label style="top:55px">Keywords:</label>
  <div class="field" style="top:64px"></div>
  <label style="top:96px">Categories</label>
  <div class="field" style="top:106px"><i class="caret"></i></div>
  <label style="top:140px">Manufacturers</label>
  <div class="field" style="top:150px"><i class="caret"></i></div>
  <div class="find-btn">FIND NOW</div>
</form>

<h1 class="abs intro-title">Vornbau.com - your online shop for model kits and detail sets.</h1>
<p class="abs intro-text">Nunc tempus felis vitae urna. Vivamus porttitor, g, purus nisi eleifend libero, a tempus libero lectus feugiat felis. Morbi diam mauris, viverra in, gravida eu, mattis in, ante. Morbi eget arcu.</p>
<ul class="abs perks" style="left:44px;top:474px">
  <li>Permanent low prices(between -10% and -50% cheaper)</li>
  <li>A big choice of model kits, figures, detail kits, tools and much more</li>
  <li>A big choice of manufacturers, from the most known to almost unknown</li>
  <li>Many articles are on stock, ready to be delivered</li>
</ul>
<ul class="abs perks" style="left:365px;top:474px">
  <li>A team of professionals at your service</li>
  <li>Fast and professional delivering</li>
  <li>The best service for you</li>
</ul>
<div class="abs rule"></div>

<h2 class="abs section-title">New Products</h2>

<div class="abs card" style="left:42px;top:620px"><div class="card-img" style="background:#2a4fd8" role="img" aria-label="Resin aircraft wheels on blue background"></div><div class="card-text">1/72 Hollmann Hm 88 wheels early (Rendall)<br>CHF 6.85</div></div>
<div class="abs card" style="left:167px;top:620px"><div class="card-img" style="background:linear-gradient(#ddd,#bbb)" role="img" aria-label="Photo-etched landing flap fret"></div><div class="card-text">1/48 Tarasov Ta-2 landing flaps (Korvak)<br>CHF 22.40</div></div>
<div class="abs card" style="left:293px;top:620px"><div class="card-img" style="background:linear-gradient(#8fb6d0,#c9b27a)" role="img" aria-label="Box art of a fighter aircraft kit"></div><div class="card-text">1/72 Seawind Stormlark Mk.4 Tropical<br>CHF 19.10</div></div>
<div class="abs card" style="left:418px;top:620px"><div class="card-img" style="background:linear-gradient(#6f88a8,#3a3a3a)" role="img" aria-label="Box art of a steam locomotive kit"></div><div class="card-text">1/72 German Feldlokomotive FL-42<br>CHF 38.20</div></div>

<div class="abs card" style="left:43px;top:780px"><div class="card-img" style="background:linear-gradient(135deg,#3a2a20,#7a8a5a)" role="img" aria-label="Box art of farm animal figures"></div><div class="card-text">1/72 Farm Animal<br>CHF 10.25</div></div>
<div class="abs card" style="left:169px;top:780px"><div class="card-img" style="background:linear-gradient(#2c2c2c,#4f5e3e)" role="img" aria-label="Box art of an aircraft kit"></div><div class="card-text">1/48 Tarasov Ta-2 landing flaps (Korvak)<br>CHF 22.40</div></div>
<div class="abs card" style="left:294px;top:780px"><div class="card-img" style="background:linear-gradient(#e0d6c6,#a8927a)" role="img" aria-label="Box art of an artillery tractor kit"></div><div class="card-text">1/35 Russian Artillery Tractor KT-7<br>CHF 41.15</div></div>
<div class="abs card" style="left:419px;top:780px"><div class="card-img" style="background:linear-gradient(135deg,#3a2418,#b5451e)" role="img" aria-label="Box art of a red triplane kit"></div><div class="card-text">1/72 Falkner Fa.3<br>Triplane<br>CHF 35.60</div></div>

<div class="abs card" style="left:44px;top:941px"><div class="card-img" style="background:linear-gradient(#5a7fa8,#3f5f88)" role="img" aria-label="Box art of a fighter aircraft in flight"></div><div class="card-text">1/72 Bruwell B3R<br>Bison<br>CHF 13.20</div></div>
<div class="abs card" style="left:169px;top:941px"><div class="card-img" style="background:linear-gradient(#c2a47a,#5c3e24)" role="img" aria-label="Box art of a military container kit"></div><div class="card-text">1/35 20' Military<br>Container<br>CHF 23.50</div></div>
<div class="abs card" style="left:295px;top:941px"><div class="card-img" style="background:linear-gradient(#7a7a6a,#b89a5a)" role="img" aria-label="Box art of a military utility vehicle kit"></div><div class="card-text">1/35 Utility Truck UT-4<br>CHF 19.10</div></div>
<div class="abs card" style="left:420px;top:941px"><div class="card-img" style="background:linear-gradient(#a8c4dc,#d0a64a)" role="img" aria-label="Box art of a fighter aircraft kit"></div><div class="card-text">1/48 Mertens<br>Mt 9E-4<br>CHF 17.15</div></div>

<aside class="abs side-box" style="left:557px;top:389px;width:198px;height:164px">
  <div class="new-head">What's New?</div>
</aside>
<div class="abs new-photo" role="img" aria-label="Photo of a camouflaged armoured vehicle model"></div>
<div class="abs new-text">1/35 CMV K7 Armored Ambulance<br>CHF 54.40</div>

<aside class="abs side-box" style="left:557px;top:565px;width:198px;height:517px">
  <div class="cat-head">Our Category</div>
</aside>
<div class="cat main" style="top:610px">Destocking</div>
<div class="cat main" style="top:629px">Planes</div>
<div class="cat sub" style="top:648px">1/144 Aircraft Decals</div>
<div class="cat sub" style="top:670px">1/144 Aircraft Kits</div>
<div class="cat sub" style="top:692px">1/144 Aircraft upgrade kit</div>
<div class="cat sub" style="top:714px">1/200 Aircraft Kits</div>
<div class="cat sub" style="top:736px">1/24 Aircraft Decals</div>
<div class="cat sub" style="top:758px">1/24 Aircraft Kits</div>
<div class="cat sub" style="top:780px">1/24 Aircraft upgrade kits</div>
<div class="cat sub" style="top:802px">1/32 Aircraft Decals</div>
<div class="cat sub" style="top:824px">1/32 Aircraft Kits</div>
<div class="cat sub" style="top:846px">1/32 Aircraft upgrade kits</div>
<div class="cat sub" style="top:868px">1/35 Aircraft Decals</div>
<div class="cat main" style="top:895px">AFV</div>
<div class="cat main" style="top:914px">Figurines</div>
<div class="cat main" style="top:933px">Car and truck</div>
<div class="cat main" style="top:951px">Ship</div>
<div class="cat main" style="top:970px">Dioramas acc.</div>
<div class="cat main" style="top:989px">Fiction</div>
<div class="cat main" style="top:1007px">Books</div>
<div class="cat main" style="top:1026px">Wargame</div>
<div class="cat main" style="top:1045px;border:none">Swiss Air Force</div>

<footer class="abs footer"></footer>
<div class="abs footer-links">Home<span>|</span>New Products<span>|</span>Sales<span>|</span>Preorder<span>|</span>About Us<span>|</span>Contact Us</div>
<div class="abs copyright">Copyright © 2013 Company Name.&nbsp; All right reserved.&nbsp; Term of Use</div>
<div class="abs social" style="left:689px;background:#3fa9e0" aria-label="Chirpline"></div>
<div class="abs social" style="left:708px;background:#1f6fa8" aria-label="Linkfold"></div>
<div class="abs social" style="left:728px;background:#3b5d9f" aria-label="Chatterly"></div>
</body>
</html>
```